Logo + Label Design (Men’s Grooming Brand & Product Packaging)

Design a logo and 2 oz pomade label for Brel, a modern men’s grooming brand focused on clean, high-quality, natural ingredients. The design should establish a bold, masculine, minimalist identity that can later extend to products like shaving gel and body wash.

Key Requirements

Create a primary logo for “Brel” and a core label for the 2 oz pomade jar (screw-top).

Use a clean, modern style — masculine, confident, and approachable (think Dorran’s, Velta, Northfield Kit).

Design for 1–2 color screen printing on solid jar colors (white, black, or navy).

Avoid gradients, foil, or embossing. Must work in black & white.

Provide: vector logo, mockup of the 2 oz jar, color palette (CMYK/RGB/HEX), and font specs.

Winning design may lead to future projects (body wash, shave gel, skincare lines).

Font styles to use
Other font styles liked:
• We like the fonts and design concept in the attached mockup.

Requirements
Should not have
• We want to avoid too much writing or busy designs. We want to avoid having graphics/illustrations embedded in the logo if they will cause the brand to look less classy or sophisticated. We also want the design to look simple and all-American (e.g. Hollister and Vane, Pine Ledger, The KIM, etc). We’d like to give a Pellham & Royce vibe that feels classy and high end.

```html
<!DOCTYPE html>
<html lang="en">
<head>
<meta charset="utf-8">
<title>Brel Hair Pomade – Label Design (Night)</title>
<link rel="stylesheet" href="https://fonts.googleapis.com/css2?family=Montserrat:wght@500;600;700&family=Barlow:wght@400;500;600&family=Barlow+Condensed:wght@500;600&display=swap">
<style>
  :root {
    --page: #ffffff;
    --label-black: #050505;
    --label-charcoal: #3d3d3d;
    --ink-white: #ffffff;
    --ink-cream: #f4f0e3;
    --ink-grey: #b4b4b4;
    --ink-soft: #9a9a9a;
    --stripe-navy: #0f3f66;
    --stripe-blue: #1b9be0;
    --ring: #ffffff;
    --ring-edge: #dcdcdc;
    --caption: #b5b5b5;
  }
  html, body {
    margin: 0;
    width: 1200px;
    height: 848px;
    overflow: hidden;
    background: var(--page);
  }
  .artboard { display: block; width: 1200px; height: 848px; }
  .display { font-family: "Montserrat", sans-serif; font-weight: 600; }
  .brand-name { font-family: "Montserrat", sans-serif; font-weight: 700; }
  .body-copy { font-family: "Barlow", sans-serif; }
  .condensed { font-family: "Barlow Condensed", sans-serif; font-weight: 600; }
  .caption { font-family: "Barlow", sans-serif; font-weight: 400; fill: var(--caption); font-size: 17px; letter-spacing: 1.2px; }
</style>
</head>
<body>
<svg class="artboard" viewBox="0 0 1200 848" xmlns="http://www.w3.org/2000/svg">
  <defs>
    <linearGradient id="label-tone" x1="0" y1="0" x2="1" y2="0">
      <stop offset="0" stop-color="var(--label-black)"/>
      <stop offset="0.55" stop-color="#141414"/>
      <stop offset="1" stop-color="var(--label-charcoal)"/>
    </linearGradient>
    <linearGradient id="side-tone" x1="0" y1="0" x2="1" y2="0">
      <stop offset="0" stop-color="#070707"/>
      <stop offset="0.5" stop-color="#000000"/>
      <stop offset="1" stop-color="#1a1a1a"/>
    </linearGradient>
    <linearGradient id="stripe" x1="0" y1="0" x2="1" y2="0">
      <stop offset="0" stop-color="var(--stripe-navy)"/>
      <stop offset="1" stop-color="var(--stripe-blue)"/>
    </linearGradient>
    <path id="lid-top-arc" d="M 687 283 A 137 137 0 0 1 945 283"/>
    <path id="lid-bottom-arc" d="M 696 399 A 139 139 0 0 0 936 399"/>
  </defs>

  <!-- Wrap-around side label, laid flat -->
  <g class="side-label">
    <rect x="134" y="420" width="460" height="160" fill="url(#side-tone)"/>
    <text class="display" x="184" y="470" font-size="31" letter-spacing="2" fill="var(--ink-cream)">HAIR</text>
    <text class="display" x="184" y="500" font-size="31" letter-spacing="2" fill="var(--ink-cream)">POMADE</text>
    <text class="body-copy" x="185" y="518" font-size="12.5" font-weight="500" letter-spacing="4.2" fill="var(--ink-cream)">FRESH &amp; CLEAN</text>
    <text class="brand-name" x="512" y="478" font-size="36" text-anchor="middle" fill="var(--ink-cream)">Brel</text>
    <rect x="176" y="527" width="380" height="3" fill="url(#stripe)"/>
    <text class="condensed" x="180" y="557" font-size="12" letter-spacing="0.6" fill="var(--ink-white)">MEDIUM HOLD <tspan font-size="7" dy="-1">◆</tspan><tspan dy="1"> MATTE FINISH</tspan></text>
    <text class="condensed" x="554" y="557" font-size="12" letter-spacing="0.6" text-anchor="end" fill="var(--ink-white)"><tspan font-weight="500">NET WT.</tspan> 2 OZ / 57 G</text>
  </g>

  <text class="caption" x="372" y="705" text-anchor="middle">LABEL DESIGN (NIGHT)</text>

  <!-- Base label (directions & ingredients) -->
  <g class="base-label">
    <circle cx="973" cy="552" r="157" fill="var(--ring)" stroke="var(--ring-edge)" stroke-width="1"/>
    <circle cx="973" cy="552" r="148" fill="url(#label-tone)"/>
    <text class="brand-name" x="975" y="463" font-size="27" text-anchor="middle" fill="var(--ink-grey)">Brel</text>
    <g class="body-copy" font-size="7" fill="var(--ink-white)" text-anchor="middle" letter-spacing="0.2">
      <text x="975" y="499"><tspan font-weight="600">DIRECTIONS:</tspan> MELT SMALL AMOUNT OF POMADE BETWEEN HANDS</text>
      <text x="975" y="509">BEFORE MASSAGING INTO DAMP HAIR (FOR SLEEKER LOOK) OR DRY HAIR</text>
      <text x="975" y="519">(FOR MORE TEXTURE). STYLE AS DESIRED. FOR EXTERNAL USE ONLY.</text>
      <text x="975" y="529">AVOID CONTACT WITH EYES. IF IRRITATION OCCURS, DISCONTINUE USE.</text>
      <text x="975" y="546"><tspan font-weight="600">INGREDIENTS:</tspan> BUTYROSPERMUM PARKII (SHEA BUTTER), CERA ALBA</text>
      <text x="975" y="556">(BEESWAX), POLYGLYCEROL-3 BEESWAX (CERA BELLINA), CAPRYLIC/CAPRIC</text>
      <text x="975" y="566">TRIGLYCERIDE (FRACTIONATED COCONUT OIL), TOCOPHEROL (VITAMIN E),</text>
      <text x="975" y="576">FRAGRANCE (PARFUM).</text>
    </g>
    <text class="body-copy" x="975" y="604" font-size="8" font-weight="600" letter-spacing="0.6" text-anchor="middle" fill="var(--ink-white)">MANUFACTURED BY:</text>
    <text class="body-copy" x="975" y="618" font-size="9.5" font-weight="600" letter-spacing="0.6" text-anchor="middle" fill="var(--ink-white)">BREL HEALTH PRODUCTS</text>
    <text class="body-copy" x="975" y="628" font-size="8" letter-spacing="0.4" text-anchor="middle" fill="var(--ink-white)">ASHFORD, NC 27945</text>
    <text class="body-copy" x="976" y="657" font-size="9.5" font-weight="600" letter-spacing="0.7" text-anchor="middle" fill="var(--ink-white)">BRELGROOMINGCO.COM</text>
  </g>

  <!-- Lid label -->
  <g class="lid-label">
    <circle cx="816" cy="329" r="157" fill="var(--ring)" stroke="var(--ring-edge)" stroke-width="1"/>
    <circle cx="816" cy="329" r="148" fill="url(#label-tone)"/>
    <text class="body-copy" font-size="7.5" letter-spacing="2.2" fill="var(--ink-soft)">
      <textPath href="#lid-top-arc" startOffset="50%" text-anchor="middle">NATURALLY DERIVED PLANT | BEE-BASED INGREDIENTS</textPath>
    </text>
    <text class="body-copy" font-size="7.5" letter-spacing="2.2" fill="var(--ink-soft)">
      <textPath href="#lid-bottom-arc" startOffset="50%" text-anchor="middle">FORMULATED TO MINIMIZE SCALP IRRITATION</textPath>
    </text>
    <text class="brand-name" x="816" y="274" font-size="38" text-anchor="middle" fill="var(--ink-white)">Brel</text>
    <rect x="694" y="315" width="251" height="4" fill="url(#stripe)"/>
    <text class="display" x="816" y="357" font-size="23" letter-spacing="2.4" text-anchor="middle" fill="var(--ink-white)">HAIR POMADE</text>
    <text class="body-copy" x="817" y="373" font-size="12" font-weight="500" letter-spacing="4.4" text-anchor="middle" fill="var(--ink-white)">FRESH &amp; CLEAN</text>
    <text class="condensed" x="817" y="419" font-size="16" letter-spacing="0.4" text-anchor="middle" fill="var(--ink-white)">2 OZ / 57 G</text>
    <text class="body-copy" x="817" y="434" font-size="12" text-anchor="middle" fill="var(--ink-white)">NET WT.</text>
  </g>
</svg>
</body>
</html>
```